Brookmere Osteopathy flyer

I want a clean clear DL flyer (but also want an A4 poster) promoting a new Osteopathic business in a semi rural area in Tasmania (Australia).
It can have pictures like the examples attached to show people what Osteopathy is (its like Chiropractic and physiotherapy).
I am the sole practioner and am male, so any pictures would be best to be a white male if possible.
I've attached some wording, you can use all, or none of it
I don't have a phone number for the business yet
info@brookmereosteopathy.example
www.brookmereosteopathy.example
Target Market(s)
Australians, from tradies, professionals, babies to retired people
Industry/Entity Type
Health
Look and feel

```html
<!DOCTYPE html>
<html lang="en">
<head>
<meta charset="utf-8">
<title>Brookmere Osteopathy – DL Flyer</title>
<link rel="stylesheet" href="https://fonts.googleapis.com/css2?family=Antonio:wght@700&family=Roboto+Condensed:wght@700&family=Arimo:wght@400;700&display=swap">
<style>
  :root {
    --page-bg: #f1f2f4;
    --panel: #e9f3fc;
    --brand-blue: #1d8fd2;
    --box-blue: #2598d8;
    --ink: #1c1c1c;
    --white: #ffffff;
    --photo-light: #f4f4f2;
    --photo-mid: #d9d6d2;
    --photo-dark: #8a7f76;
  }
  * { box-sizing: border-box; margin: 0; padding: 0; }
  html, body {
    width: 960px; height: 1200px; overflow: hidden;
    background: var(--page-bg);
  }
  .flyer {
    position: absolute; left: 211px; top: 30px;
    width: 538px; height: 1140px;
    background: var(--panel);
    box-shadow: 0 6px 18px rgba(0,0,0,0.12);
    font-family: "Arimo", Arial, sans-serif;
    color: var(--ink);
    overflow: hidden;
  }
  .header-rule, .photo-rule {
    position: absolute; left: 0; width: 100%; height: 5px;
    background: var(--brand-blue);
  }
  .header-rule { top: 175px; }
  .photo-rule { top: 465px; }
  .hero-photo {
    position: absolute; left: 0; top: 180px; width: 100%; height: 285px;
    background: linear-gradient(160deg, var(--photo-light) 0%, var(--photo-mid) 55%, var(--photo-dark) 100%);
  }
  .brand-seal {
    position: absolute; left: 27px; top: 27px; width: 200px; height: 200px;
    z-index: 2;
    border-radius: 50%; background: var(--white);
    border: 6px solid var(--brand-blue);
    display: flex; align-items: center; justify-content: center;
    text-align: center;
    font-family: "Roboto Condensed", "Arial Narrow", sans-serif;
    font-weight: 700; font-size: 22px; line-height: 1.15;
    color: var(--brand-blue); text-transform: uppercase;
  }
  .brand-title {
    position: absolute; left: 250px; top: 42px;
    font-family: "Antonio", "Arial Narrow", sans-serif;
    font-weight: 700; font-size: 57px; line-height: 60px;
    color: var(--brand-blue); white-space: nowrap;
  }
  .reasons-heading {
    position: absolute; left: 37px; top: 487px;
    font-family: "Roboto Condensed", "Arial Narrow", sans-serif;
    font-weight: 700; font-size: 24px; color: var(--brand-blue);
    white-space: nowrap;
  }
  .reasons-list {
    position: absolute; left: 37px; top: 527px; list-style: none;
    font-size: 21px; line-height: 27.6px;
  }
  .reasons-list li { position: relative; padding-left: 27px; white-space: nowrap; }
  .reasons-list li::before {
    content: ""; position: absolute; left: 4px; top: 10px;
    width: 8px; height: 8px; background: var(--brand-blue);
    transform: rotate(45deg);
  }
  .about-box {
    position: absolute; left: 35px; top: 818px; width: 468px; height: 158px;
    background: var(--box-blue); border-radius: 16px;
    padding: 9px 14px; color: var(--white);
    font-size: 22px; line-height: 28px; text-align: justify;
  }
  .contact-list {
    position: absolute; left: 47px; top: 985px; list-style: none;
  }
  .contact-list li {
    display: flex; align-items: center; height: 34px;
    font-size: 20.5px; white-space: nowrap;
  }
  .contact-list li.contact-phone { font-weight: 700; font-size: 27px; height: 36px; }
  .contact-icon {
    width: 22px; height: 22px; border-radius: 4px;
    background: var(--brand-blue); margin-right: 14px; flex: none;
  }
</style>
</head>
<body>
<article class="flyer">
  <div class="hero-photo" role="img" aria-label="Photo of an osteopath treating a patient's shoulder while she lies on a treatment table"></div>
  <div class="header-rule"></div>
  <div class="photo-rule"></div>
  <div class="brand-seal">Brookmere<br>Osteopathy</div>
  <h1 class="brand-title">BROOKMERE<br>OSTEOPATHY</h1>

  <h2 class="reasons-heading">Common reasons people visit an osteopath:</h2>
  <ul class="reasons-list">
    <li>Back / neck pain</li>
    <li>Headaches / migraines</li>
    <li>Joint and muscle pain</li>
    <li>Pregnancy-related discomfort</li>
    <li>Disc related issues</li>
    <li>Sciatica</li>
    <li>Plantar fasciitis</li>
    <li>Tendonitis / Bursitis</li>
    <li>Adhesive capsulitis (frozen shoulder)</li>
    <li>Tennis / Golfers elbow</li>
  </ul>

  <p class="about-box">Osteopaths use a combination of joint manipulation, targeted deep tissue massage and stretching to improve function, relieve pain and support the body’s ability to heal itself</p>

  <ul class="contact-list">
    <li>
      <svg class="contact-icon" viewBox="0 0 22 22" aria-hidden="true"><rect width="22" height="22" rx="4" fill="#1d8fd2"/><path d="M11 4a5 5 0 0 0-5 5c0 4 5 9 5 9s5-5 5-9a5 5 0 0 0-5-5z" fill="none" stroke="#fff" stroke-width="1.8"/><circle cx="11" cy="9" r="1.8" fill="#fff"/></svg>
      24 Quarry Lane, Brookmere
    </li>
    <li class="contact-phone">
      <svg class="contact-icon" viewBox="0 0 22 22" aria-hidden="true"><rect width="22" height="22" rx="4" fill="#1d8fd2"/><path d="M8 4h3l1 4-2 1.5c.8 1.8 1.7 2.7 3.5 3.5L15 11l4 1v3c0 1-1 2-2 2C10 17 5 12 5 6c0-1 1-2 3-2z" fill="#fff"/></svg>
      000 000 0000
    </li>
    <li>
      <svg class="contact-icon" viewBox="0 0 22 22" aria-hidden="true"><rect width="22" height="22" rx="4" fill="#1d8fd2"/><g fill="none" stroke="#fff" stroke-width="1.4"><circle cx="11" cy="11" r="6.5"/><ellipse cx="11" cy="11" rx="3" ry="6.5"/><path d="M4.5 11h13M5.5 7.5h11M5.5 14.5h11"/></g></svg>
      www.brookmereosteopathy.example
    </li>
    <li>
      <svg class="contact-icon" viewBox="0 0 22 22" aria-hidden="true"><rect width="22" height="22" rx="4" fill="#1d8fd2"/><rect x="4.5" y="6.5" width="13" height="9" rx="1" fill="none" stroke="#fff" stroke-width="1.6"/><path d="M4.5 7l6.5 5 6.5-5" fill="none" stroke="#fff" stroke-width="1.6"/></svg>
      info@brookmereosteopathy.example
    </li>
  </ul>
</article>
</body>
</html>
```